Graphic Design of Business Process

We require an eye-catching, sophisticated design of 2 business processes (attached), that will be used digitally AND for print (to be put on walls in our office).

The basic layout is attached. We require a creative, professional designer to re-design these so that they look appealing but still able to grasp all the information.

We will require vector files and editable project files for final delivery. You may refer to our website (quillharbourworks.com.au) for an indication of our brand.

If you have any questions, please ask.

Thank you.

```html
<!DOCTYPE html>
<html lang="en">
<head>
<meta charset="utf-8">
<title>Sales Content Funnel</title>
<link rel="stylesheet" href="https://fonts.googleapis.com/css2?family=Fira+Sans+Condensed:wght@500;600;700&family=Poppins:wght@700&family=Quicksand:wght@400&display=swap">
<style>
  :root {
    --charcoal: #3a3a3a;
    --paper: #e6e7e8;
    --red: #ec4a4a;
    --red-deep: #e3302f;
    --orange: #f9a61c;
    --orange-deep: #f7941d;
    --green: #4daf52;
    --green-deep: #3f9e46;
    --blue: #2bbad3;
    --blue-deep: #1aaac8;
    --purple: #7c5ea9;
    --brown: #a34a1e;
    --forest: #1f5f2a;
    --navy: #17587f;
    --white: #ffffff;
    --ink: #111111;
  }
  html, body { margin: 0; padding: 0; overflow: hidden; background: var(--charcoal); }
  .canvas { display: block; width: 958px; height: 1200px; }
  .funnel-text { font-family: "Fira Sans Condensed", "Arial Narrow", sans-serif; text-anchor: middle; }
  .title-xl { font-size: 104px; font-weight: 700; fill: var(--white); }
  .title-lg { font-size: 60px; font-weight: 700; fill: var(--white); }
  .title-md { font-size: 46px; font-weight: 600; fill: var(--white); }
  .title-sm { font-size: 30px; font-weight: 600; fill: var(--white); }
  .kicker { font-size: 21px; font-weight: 600; }
  .bullet { font-size: 21px; font-weight: 600; fill: var(--white); }
  .u { text-decoration: underline; }
  .step-text { font-family: "Fira Sans Condensed", "Arial Narrow", sans-serif; font-weight: 600; }
  .legend-name { font-family: "Poppins", sans-serif; font-weight: 700; font-size: 86px; }
  .legend-note { font-family: "Quicksand", sans-serif; font-weight: 400; font-size: 46px; }
  .flow { fill: none; stroke: var(--ink); stroke-width: 11; stroke-linecap: round; }
</style>
</head>
<body>
<svg class="canvas" viewBox="0 0 1200 1503" xmlns="http://www.w3.org/2000/svg" aria-label="Sales content funnel with hero, hub and hygiene content types">
  <defs>
    <marker id="arrowhead" viewBox="0 0 10 10" refX="6" refY="5" markerWidth="4" markerHeight="4" orient="auto-start-reverse">
      <path d="M0 0 L10 5 L0 10 z" fill="var(--ink)"/>
    </marker>
  </defs>

  <!-- backgrounds -->
  <rect class="top-band" x="0" y="0" width="1200" height="43" fill="var(--charcoal)"/>
  <rect class="stage" x="0" y="43" width="1200" height="862" fill="var(--paper)"/>
  <rect class="legend-band" x="0" y="905" width="1200" height="598" fill="var(--charcoal)"/>

  <!-- funnel bands -->
  <g class="funnel">
    <polygon points="58,217 873,217 800,368 133,368" fill="var(--red)"/>
    <polygon points="133,368 800,368 727,519 207,519" fill="var(--orange)"/>
    <polygon points="207,519 727,519 655,669 281,669" fill="var(--green)"/>
    <polygon points="281,669 655,669 578,828 360,828" fill="var(--blue)"/>
    <polygon class="funnel-light" points="58,217 112,217 372,828 360,828" fill="#ffffff" opacity="0.3"/>
    <polygon class="funnel-shade" points="720,217 873,217 578,828 515,828" fill="#000000" opacity="0.06"/>
  </g>

  <g class="funnel-text">
    <text class="title-xl" x="476" y="310">SALES</text>
    <text class="title-sm" x="476" y="354">Content Funnel</text>

    <text class="title-lg" x="472" y="420">AWARENESS</text>
    <text class="kicker" x="472" y="446" fill="var(--brown)">IDENTIFY PROBLEM/NEED</text>
    <text class="bullet" x="470" y="470">• Aspirational</text>
    <text class="bullet" x="466" y="502">• Market The <tspan class="u">Outcome</tspan> Not Product</text>

    <text class="title-md" x="469" y="557">CONSIDERATION</text>
    <text class="kicker" x="467" y="582" fill="var(--forest)">EVALUATE ALTERNATIVES</text>
    <text class="bullet" x="468" y="609">•Why is <tspan class="u">this solution</tspan> better than others</text>
    <text class="bullet" x="468" y="635">• <tspan class="u">How</tspan> is the provider going to solve</text>
    <text class="bullet" x="474" y="656">my need</text>

    <text class="title-sm" x="466" y="703">ACTION/DECISION</text>
    <text class="kicker" x="466" y="726" font-size="18" fill="var(--navy)">PRESENT AN OFFER</text>
    <text class="bullet" x="461" y="756">• <tspan class="u">Which</tspan> Provider?</text>
  </g>

  <!-- journey steps -->
  <g class="steps">
    <polygon points="818,383 1096,383 1043,502 768,502" fill="var(--orange)"/>
    <text class="step-text" x="944" y="419" text-anchor="middle" font-size="27" fill="var(--brown)">Problem &amp; Solution</text>
    <text class="step-text" x="910" y="451" text-anchor="middle" font-size="23" fill="var(--white)">• Subject Showing</text>
    <text class="step-text" x="918" y="476" text-anchor="middle" font-size="23" fill="var(--white)">Symptons of Problems</text>

    <polygon points="740,551 1018,551 965,665 692,665" fill="var(--green)"/>
    <text class="step-text" x="870" y="580" text-anchor="middle" font-size="26" fill="var(--forest)">Providers &amp; Types of</text>
    <text class="step-text" x="870" y="604" text-anchor="middle" font-size="26" fill="var(--forest)">Solution</text>
    <text class="step-text" x="718" y="632" font-size="23" fill="var(--white)">•Subject Gives</text>
    <text class="step-text" x="710" y="657" font-size="23" fill="var(--white)">Name to Problem</text>

    <polygon points="668,719 942,719 918,769 643,769" fill="var(--blue)"/>
    <text class="step-text" x="792" y="751" text-anchor="middle" font-size="27" fill="var(--navy)">Convert &amp; Retain</text>

    <polygon points="615,817 834,817 822,856 603,856" fill="var(--purple)"/>
    <text class="step-text" x="717" y="843" text-anchor="middle" font-size="22" fill="var(--white)">Wom &amp; Referral</text>
  </g>

  <!-- flow arrows -->
  <g class="flow-arrows">
    <path class="flow" d="M1098,445 C1170,480 1160,580 1030,600" marker-start="url(#arrowhead)" marker-end="url(#arrowhead)"/>
    <path class="flow" d="M1045,612 C1100,650 1095,730 960,742" marker-end="url(#arrowhead)"/>
    <path class="flow" d="M965,750 C1015,775 1010,825 900,828 L835,830"/>
    <path class="flow" d="M612,830 L585,829" marker-end="url(#arrowhead)"/>
  </g>

  <!-- content types legend -->
  <g class="legend">
    <rect x="50" y="963" width="75" height="138" fill="var(--orange)"/>
    <rect x="125" y="1096" width="585" height="5" fill="var(--orange)"/>
    <text class="legend-name" x="150" y="1025" fill="var(--orange)">Hero</text>
    <text class="legend-note" x="150" y="1085" fill="var(--orange)">Tentpole Campaigns</text>

    <rect x="50" y="1116" width="75" height="137" fill="var(--green)"/>
    <rect x="125" y="1248" width="585" height="5" fill="var(--green)"/>
    <text class="legend-name" x="150" y="1178" fill="var(--green)">Hub</text>
    <text class="legend-note" x="150" y="1238" fill="var(--green)">Regular “Push” Content</text>

    <rect x="50" y="1268" width="75" height="137" fill="var(--blue)"/>
    <rect x="125" y="1400" width="585" height="5" fill="var(--blue)"/>
    <text class="legend-name" x="150" y="1330" fill="var(--blue)">Hygiene</text>
    <text class="legend-note" x="150" y="1390" fill="var(--blue)">Always-on “Pull” Content</text>
  </g>
</svg>
</body>
</html>
```